PitchTally Webpages and Logo

See attached brief. Take the existing website www.pitchtally.co.uk and logo and transform these assets to:

Give people who arrive on the site for first time the confidence to sign-up easily and quickly
Allow regular returning users quick and easy placing of predictions and encourage them to share the PitchTally prediction on social networks and with their contacts
Convey the essence of a community working together to enjoyably come-up with smart predictions on sporting events
Work seamlessly and well across smartphones, tablets and desktop i.e. Should be Responsive Web Design
Updates

Target Market(s)

Users are sports fans with opinions
Primarily male and early twenties to mid-thirties
They are competitive - they want to beat their peers
Many are from outside the UK

Industry/Entity Type

Events

Logo Text

PitchTally

Coding

Coded - Design and coding required

Number of Pages Required

4 page

Font styles to use
Sans Serif

Requirements
Must have
• Responsive Web Design
• Mobile First
• HTML must work with dedicated bespoke application developed in ASP.NET using MS SQL underneath
• See Brief
Nice to have
• See brief
Should not have
• See brief

```html
<!DOCTYPE html>
<html lang="en">
<head>
<meta charset="utf-8">
<title>PitchTally – Predict and Win</title>
<link rel="stylesheet" href="https://fonts.googleapis.com/css2?family=Open+Sans:wght@400;600;700&family=Marcellus&display=swap">
<style>
:root{
  --pink:#d63a83;
  --pink-dark:#b82a6c;
  --black:#050505;
  --ink:#222;
  --muted:#666;
  --card:#f2f2f2;
  --footer:#2b2b2b;
  --footer-text:#bcbcbc;
  --white:#fff;
}
*{box-sizing:border-box;margin:0;padding:0}
html,body{width:780px;height:1200px;overflow:hidden}
body{font-family:"Open Sans",sans-serif;color:var(--ink);background:var(--white);position:relative}
a{color:inherit;text-decoration:none}

.topbar{height:32px;background:var(--black);color:var(--white);display:flex;align-items:center;padding:0 38px;font-size:10px}
.kitty-rate{color:#4fd36b;font-weight:700;margin-left:4px;font-size:8px}
.share{display:flex;margin-left:14px;background:#f3f3f3;border-radius:2px;height:14px;width:114px;font-size:8px;color:#4a79b6;align-items:center;justify-content:space-around}
.account{margin-left:auto;display:flex;gap:6px}
.account a{background:var(--pink);border:1px solid #f07bb3;border-radius:2px;width:74px;height:20px;display:flex;align-items:center;justify-content:center;font-size:10px}

.mainnav{height:55px;display:flex;align-items:center;padding:0 38px;border-bottom:1px solid #e5e5e5}
.brand{display:flex;align-items:center;gap:6px;font-size:19px;font-weight:700;color:var(--pink)}
.brand-mark{width:40px;height:40px;border-radius:6px;background:var(--pink)}
.menu{display:flex;margin-left:auto;gap:0;font-size:10px;margin-right:8px}
.menu a{margin-left:37px}

.hero{position:relative;height:347px;background:linear-gradient(180deg,#8a7a62 0%,#5b5344 35%,#3f3a30 60%,#4c5a35 82%,#5f7040 100%);color:var(--white);text-align:center;overflow:hidden}
.hero-title{padding-top:34px;font-size:24px;font-weight:400;line-height:35px}
.hero-title em{font-style:normal;color:var(--pink);font-weight:700}
.hero-copy{font-family:"Marcellus",serif;font-size:11.5px;line-height:24px;margin:4px auto 0;width:560px}
.join{display:inline-block;margin-top:20px;width:148px;height:39px;background:var(--pink);border:2px solid #e96aa7;font-size:17px;font-weight:700;line-height:35px}
.arrow{position:absolute;top:168px;font-size:14px;color:#ccc}
.arrow.prev{left:40px}.arrow.next{right:40px}
.tips{position:absolute;left:-40px;top:44px;width:180px;height:22px;background:var(--white);color:var(--pink);transform:rotate(-45deg);font-size:10px;line-height:22px;text-align:center;font-style:italic}
.stats{position:absolute;left:120px;top:236px;width:554px;height:70px;border:1px solid rgba(255,255,255,.7);background:rgba(255,255,255,.55);display:flex;color:var(--black)}
.stat{flex:1;padding-top:8px}
.stat-head{color:var(--white);font-size:11px;letter-spacing:.3px}
.stat-head span{margin-left:14px}
.stat-value{font-size:8.5px;font-weight:600;margin-top:12px;line-height:13px}
.stats .dot{align-self:center;font-size:8px}

.steps{position:absolute;left:38px;top:419px;width:702px;height:104px;background:var(--black);color:var(--white);display:flex;box-shadow:0 3px 6px rgba(0,0,0,.3)}
.step{flex:1;display:flex;gap:10px;padding:22px 14px 0 22px;border-right:1px solid #555}
.step:last-child{border-right:0}
.step-icon{width:52px;height:52px;flex:none;border-radius:4px;background:linear-gradient(135deg,#ee6aa9,#b82a6c);margin-top:8px}
.step h3{font-size:14px;font-weight:400;margin-bottom:4px}
.step p{font-size:7.5px;line-height:15px;color:#ddd}

.section-title{position:absolute;top:544px;width:100%;text-align:center;color:var(--pink);font-size:14px;font-weight:700}
.fixtures{position:absolute;left:39px;top:582px;width:701px;display:grid;grid-template-columns:repeat(3,225px);column-gap:13px;row-gap:37px}
.fixture{height:178px;background:var(--card);display:flex;flex-direction:column}
.teams{display:flex;justify-content:space-between;align-items:center;padding:26px 27px 0 27px}
.crest{width:60px;height:60px;border-radius:50%;background:var(--white)}
.versus{font-size:13px}
.names{display:flex;justify-content:space-between;padding:11px 18px 0 18px;color:var(--pink);font-size:10px}
.kickoff{text-align:center;font-size:8.5px;margin-top:10px}
.kickoff svg{vertical-align:-2px;margin-right:8px}
.predict{margin-top:auto;height:37px;background:var(--pink);color:var(--white);font-size:13.5px;font-weight:700;display:flex;align-items:center;justify-content:center}
.show-all{position:absolute;top:992px;width:100%;text-align:center;color:var(--pink);font-size:12px}

.footer{position:absolute;top:1027px;left:0;width:780px;height:173px;background:var(--footer);color:var(--footer-text)}
.footer h4{color:var(--pink);font-weight:400;font-size:12px;margin-bottom:6px}
.links{position:absolute;top:18px;font-size:7.5px;line-height:10.8px}
.links.useful{left:39px}.links.help{left:164px}
.feedback{position:absolute;left:294px;top:21px;width:189px;height:31px;border:1px solid var(--pink);color:var(--pink);font-size:11px;display:flex;align-items:center;justify-content:center;gap:12px}
.social{position:absolute;left:298px;top:87px;display:flex;gap:7px}
.social span{width:25px;height:24px;background:#e5e5e5;border-radius:2px;display:flex;align-items:center;justify-content:center}
.copyright{position:absolute;top:146px;left:0;width:780px;text-align:center;font-size:6.5px;color:#ddd}
.pundits{position:absolute;left:536px;top:19px;width:180px}
.pundits h4{text-align:center}
.pundit-photo{width:50px;height:50px;border-radius:50%;background:linear-gradient(#cfd6dc,#8c949b);margin:6px auto 0;border:2px solid #fff}
.pundits p{font-size:7.5px;line-line:13px;line-height:13px;margin-top:10px}
.pundits cite{display:block;text-align:right;font-style:normal;color:var(--white);font-size:9px;margin-top:3px}
</style>
</head>
<body>
<header>
  <div class="topbar">
    <span>Kitty: £1289 <span class="kitty-rate">▲5%</span></span>
    <div class="share"><span>Tweet</span><span>Share</span></div>
    <nav class="account"><a href="#">Login</a><a href="#">Register</a></nav>
  </div>
  <div class="mainnav">
    <a class="brand" href="#"><span class="brand-mark"></span>PitchTally</a>
    <nav class="menu">
      <a href="#">Home</a><a href="#">About Us</a><a href="#">Tables</a><a href="#">Kitty</a><a href="#">FAQ</a><a href="#">History</a><a href="#">Contact</a>
    </nav>
  </div>
</header>

<section class="hero" role="img" aria-label="Floodlit football stadium with crowd and pitch">
  <div class="tips">PitchTally Hot Tips!!</div>
  <h1 class="hero-title">Predict 6 scores<br>to win <em>£250,000</em></h1>
  <p class="hero-copy">MAECENAS A SAPIEN TORTOR QUIS TINCIDUNT LECTUS. DONEC ULLAMCORPER DUI SIT AMET LOREM ULTRICES SED PORTTITOR MASSA EU DUI SCELERISQUE</p>
  <a class="join" href="#">JOIN NOW</a>
  <span class="arrow prev">&#10094;</span><span class="arrow next">&#10095;</span>
  <div class="stats">
    <div class="stat"><div class="stat-head">RESULT<span>100%</span></div><div class="stat-value">NORTHGATE CITY WIN</div></div>
    <span class="dot">◆</span>
    <div class="stat"><div class="stat-head">SCORE<span>50%</span></div><div class="stat-value">EASTBROOK VILLA 0<br>WESTFORD UNITED 2</div></div>
    <span class="dot">◆</span>
    <div class="stat"><div class="stat-head">1st GOAL<span>80%</span></div><div class="stat-value">BARLOW C</div></div>
  </div>
</section>

<section class="steps">
  <div class="step"><div class="step-icon" role="img" aria-label="Padlock with users icon"></div><div><h3>Log in</h3><p>Maecenas a sapien tortor quis tincidt lectus. Donec ullamcorper dui sit am lorem ultrices sed......»</p></div></div>
  <div class="step"><div class="step-icon" role="img" aria-label="Puzzle piece icon"></div><div><h3>Predict</h3><p>Maecenas a sapien tortor quis tincidt lectus. Donec ullamcorper dui sit am lorem ultrices sed porttitor massa</p></div></div>
  <div class="step"><div class="step-icon" role="img" aria-label="Treasure chest icon"></div><div><h3>Enjoy</h3><p>Maecenas a sapien tortor quis tincidt lectus. Donec ullamcorper dui sit am lorem ultrices sed porttitor massa</p></div></div>
</section>

<h2 class="section-title">TEMPOR INCIDIDUNT</h2>

<main class="fixtures">
  <article class="fixture"><div class="teams"><span class="crest"></span><span class="versus">V</span><span class="crest"></span></div><div class="names"><span>Northgate City</span><span>Riverside Palace</span></div><p class="kickoff"><svg width="9" height="9" viewBox="0 0 10 10"><circle cx="5" cy="5" r="4" fill="none" stroke="#d63a83" stroke-width="1.4"/><path d="M5 3v2h2" stroke="#d63a83" fill="none"/></svg>Sat 20 Dec 2014 12:45 PM</p><a class="predict" href="#">Predict Score Now!</a></article>
  <article class="fixture"><div class="teams"><span class="crest"></span><span class="versus">V</span><span class="crest"></span></div><div class="names"><span>Northgate City</span><span>Riverside Palace</span></div><p class="kickoff"><svg width="9" height="9" viewBox="0 0 10 10"><circle cx="5" cy="5" r="4" fill="none" stroke="#d63a83" stroke-width="1.4"/><path d="M5 3v2h2" stroke="#d63a83" fill="none"/></svg>Sat 20 Dec 2014 12:45 PM</p><a class="predict" href="#">Predict Score Now!</a></article>
  <article class="fixture"><div class="teams"><span class="crest"></span><span class="versus">V</span><span class="crest"></span></div><div class="names"><span>Northgate City</span><span>Riverside Palace</span></div><p class="kickoff"><svg width="9" height="9" viewBox="0 0 10 10"><circle cx="5" cy="5" r="4" fill="none" stroke="#d63a83" stroke-width="1.4"/><path d="M5 3v2h2" stroke="#d63a83" fill="none"/></svg>Sat 20 Dec 2014 12:45 PM</p><a class="predict" href="#">Predict Score Now!</a></article>
  <article class="fixture"><div class="teams"><span class="crest"></span><span class="versus">V</span><span class="crest"></span></div><div class="names"><span>Northgate City</span><span>Riverside Palace</span></div><p class="kickoff"><svg width="9" height="9" viewBox="0 0 10 10"><circle cx="5" cy="5" r="4" fill="none" stroke="#d63a83" stroke-width="1.4"/><path d="M5 3v2h2" stroke="#d63a83" fill="none"/></svg>Sat 20 Dec 2014 12:45 PM</p><a class="predict" href="#">Predict Score Now!</a></article>
  <article class="fixture"><div class="teams"><span class="crest"></span><span class="versus">V</span><span class="crest"></span></div><div class="names"><span>Northgate City</span><span>Riverside Palace</span></div><p class="kickoff"><svg width="9" height="9" viewBox="0 0 10 10"><circle cx="5" cy="5" r="4" fill="none" stroke="#d63a83" stroke-width="1.4"/><path d="M5 3v2h2" stroke="#d63a83" fill="none"/></svg>Sat 20 Dec 2014 12:45 PM</p><a class="predict" href="#">Predict Score Now!</a></article>
  <article class="fixture"><div class="teams"><span class="crest"></span><span class="versus">V</span><span class="crest"></span></div><div class="names"><span>Northgate City</span><span>Riverside Palace</span></div><p class="kickoff"><svg width="9" height="9" viewBox="0 0 10 10"><circle cx="5" cy="5" r="4" fill="none" stroke="#d63a83" stroke-width="1.4"/><path d="M5 3v2h2" stroke="#d63a83" fill="none"/></svg>Sat 20 Dec 2014 12:45 PM</p><a class="predict" href="#">Predict Score Now!</a></article>
</main>

<a class="show-all" href="#">Show All &nbsp;<svg width="13" height="11" viewBox="0 0 13 11"><path d="M1 5h7M5 2l3 3-3 3" stroke="#d63a83" stroke-width="1.4" fill="none"/><rect x="8.5" y="1" width="3.5" height="9" rx="1" fill="none" stroke="#d63a83"/></svg></a>

<footer class="footer">
  <div class="links useful"><h4>USEFUL LINKS</h4>Home<br>About Us<br>Tables<br>Kitty<br>FAQ<br>Profile<br>History<br>Mini-Liga Admin<br>Contact</div>
  <div class="links help"><h4>HELP</h4>Login<br>Register<br>Terms<br>Site Map<br>Privacy<br>Terms and Conditions</div>
  <a class="feedback" href="#"><svg width="11" height="9" viewBox="0 0 11 9"><rect x=".5" y=".5" width="10" height="8" fill="none" stroke="#d63a83"/><path d="M.5 .5l5 4 5-4" fill="none" stroke="#d63a83"/></svg>Send Us Feedback</a>
  <div class="social">
    <span><svg width="10" height="8" viewBox="0 0 10 8"><rect width="10" height="8" fill="#333"/><path d="M0 0l5 4 5-4" fill="none" stroke="#e5e5e5"/></svg></span>
    <span></span><span></span><span></span><span></span><span></span>
  </div>
  <div class="pundits">
    <h4>PUNDITS PREDICTIONS</h4>
    <div class="pundit-photo" role="img" aria-label="Portrait of the pundit"></div>
    <p>Sed ut perspiciatis unde omnis iste natus error sit voluptatem &nbsp;doloremque.....</p>
    <cite>By Dan Hollis</cite>
  </div>
  <p class="copyright">Copyright © PitchTally 2014. All Rights Reserved.</p>
</footer>
</body>
</html>
```